Business Cards for IT Consulting Company (Managed Service Provider)

I am looking to have some business cards printed and would like some designs. We are an IT Consulting company based in Vancouver BC. I would like a nice clean and modern look to the cards. I have uploaded all the versions of my logo so parts can be used as needed. Here is a snippit from our website homepage:

Quillbrook Networks Ltd. is an IT Solutions Partner located in Vancouver BC, Canada. We offer IT solutions and support to customers in the greater Vancouver Area. With expertise in Microsoft platforms, as well as Linux and Mac OSX and over 12 years experience in the IT industry, Quillbrook Networks is dedicated to offering our clients top quality service and products. We take pride in the solutions we offer our customers. The greatest compliment a client can give us is to recommend our services.

Quillbrook Networks Ltd. offers a wide range of IT services from onsite service to remote support and managed service solutions. This allows clients to choose the support path that best suits their company’s needs. Supporting many different sized companies from small to enterprise level over the past 12 years Quillbrook Networks has the experience and expertise needed to ensure things run smoothly. Allowing our clients to focus on doing business.

Revolutionizing the way IT services are delivered.

Quillbrook Networks is dedicated to providing our clients with IT solutions that work and grow with them for years to come. This philosophy helps save money in the long run instead of replacing equipment constantly. Far too often IT solutions are not well thought out and while possibly solving the problem at hand, require replacement due to growth or quality within a very short time frame. Quillbrook Networks takes pride in providing solutions that will last and be able to accommodate growth without the need for replacement.

Industry/Entity Type

Information Technology

Contact Information for Business Card

Quillbrook Networks Ltd.
(Employee Name)
Eml: (Employees Email Address)
Web: quillbrook.me
Ph: 604-555-0148

Font styles to use
Serif
Sans Serif

Requirements
Must have
• The Company logo and company colors.
Nice to have
• - Our tag line: "Revolutionizing IT Services" or "Revolutionizing the way IT services are delivered."
• - Also I really like the idea of nature and technology together blending which is sort of where my logo came from so integrating that somehow onto the business cards would be great.

```html
<!DOCTYPE html>
<html lang="en">
<head>
<meta charset="UTF-8">
<title>Quillbrook Networks Ltd. – Business Cards</title>
<link rel="stylesheet" href="https://fonts.googleapis.com/css2?family=Montserrat:wght@600;700&family=Roboto:ital,wght@0,400;1,400&display=swap">
<style>
  :root {
    --bg: #e6e6e6;
    --card: #f4f4f4;
    --brand-blue: #1a8fd6;
    --brand-dark: #4a4a4c;
    --text-grey: #444446;
    --muted: #5a5a5c;
  }
  * { margin: 0; padding: 0; box-sizing: border-box; }
  html, body { width: 1200px; height: 1200px; overflow: hidden; }
  body {
    position: relative;
    background: var(--bg);
    font-family: "Roboto", Arial, sans-serif;
    color: var(--text-grey);
  }
  .card {
    position: absolute;
    width: 712px;
    height: 418px;
    background: var(--card);
    overflow: hidden;
  }
  .card--front { left: 238px; top: 119px; }
  .card--back  { left: 231px; top: 644px; height: 416px; }

  .wordmark {
    position: absolute;
    display: flex;
    align-items: center;
    gap: 14px;
    font-family: "Montserrat", Arial, sans-serif;
    font-weight: 600;
    color: var(--brand-blue);
    white-space: nowrap;
  }
  .wordmark__square {
    background: var(--brand-blue);
    flex: none;
  }
  .card--front .wordmark {
    left: 0; right: 0; top: 158px;
    justify-content: center;
    font-size: 34px;
  }
  .card--front .wordmark__square { width: 34px; height: 34px; }

  .tagline {
    position: absolute;
    left: 0; right: 0; top: 376px;
    display: flex;
    justify-content: center;
    align-items: center;
    gap: 16px;
    font-size: 18px;
    color: var(--text-grey);
  }
  .tagline__rule {
    width: 112px;
    height: 3px;
    background: linear-gradient(90deg, rgba(26,143,214,0) 0%, var(--brand-blue) 40%);
  }
  .tagline__rule--right {
    background: linear-gradient(270deg, rgba(26,143,214,0) 0%, var(--brand-blue) 40%);
  }

  .side-band {
    position: absolute;
    left: 0; top: 0; bottom: 0;
    width: 60px;
    background: var(--brand-blue);
  }
  .side-band__edge {
    position: absolute;
    left: 60px; top: 0; bottom: 0;
    width: 8px;
    background: var(--brand-dark);
  }
  .card--back .wordmark {
    left: 107px; top: 70px;
    font-size: 30px;
    gap: 12px;
  }
  .card--back .wordmark__square { width: 30px; height: 30px; }

  .person {
    position: absolute;
    left: 107px; top: 204px;
  }
  .person__name {
    font-family: "Montserrat", Arial, sans-serif;
    font-weight: 700;
    font-size: 24px;
    color: var(--brand-blue);
    line-height: 1.2;
  }
  .person__role {
    margin-top: 4px;
    font-style: italic;
    font-size: 16px;
    color: var(--muted);
  }

  .contact-list {
    position: absolute;
    left: 106px; top: 294px;
    list-style: none;
  }
  .contact-list__item {
    display: flex;
    align-items: center;
    height: 27.5px;
    font-size: 17.5px;
    color: var(--text-grey);
  }
  .contact-list__icon {
    width: 18px; height: 18px;
    margin-right: 16px;
    fill: var(--brand-blue);
    flex: none;
  }
</style>
</head>
<body>

<section class="card card--front" aria-label="Business card front">
  <div class="wordmark">
    <span class="wordmark__square"></span>
    <span class="wordmark__name">Quillbrook Networks Ltd.</span>
  </div>
  <div class="tagline">
    <span class="tagline__rule"></span>
    <span class="tagline__text">Revolutionizing IT Services</span>
    <span class="tagline__rule tagline__rule--right"></span>
  </div>
</section>

<section class="card card--back" aria-label="Business card back">
  <div class="side-band"></div>
  <div class="side-band__edge"></div>

  <div class="wordmark">
    <span class="wordmark__square"></span>
    <span class="wordmark__name">Quillbrook Networks Ltd.</span>
  </div>

  <div class="person">
    <p class="person__name">Daniel Hart</p>
    <p class="person__role">Managing Director</p>
  </div>

  <ul class="contact-list">
    <li class="contact-list__item">
      <svg class="contact-list__icon" viewBox="0 0 20 20" aria-hidden="true">
        <path d="M2 6c0-2 3-3.5 8-3.5S18 4 18 6v1.5h-4.5V5.8c-1-.4-2.2-.5-3.5-.5s-2.5.1-3.5.5v1.7H2z"/>
        <path d="M6 9h8l3 7.5H3z"/>
      </svg>
      <span>604-555-0148</span>
    </li>
    <li class="contact-list__item">
      <svg class="contact-list__icon" viewBox="0 0 20 20" aria-hidden="true">
        <circle cx="10" cy="10" r="8"/>
        <g fill="none" stroke="#f4f4f4" stroke-width="1.2">
          <ellipse cx="10" cy="10" rx="3.5" ry="8"/>
          <line x1="2" y1="10" x2="18" y2="10"/>
          <line x1="3.5" y1="6" x2="16.5" y2="6"/>
          <line x1="3.5" y1="14" x2="16.5" y2="14"/>
        </g>
      </svg>
      <span>www.quillbrook.me</span>
    </li>
    <li class="contact-list__item">
      <svg class="contact-list__icon" viewBox="0 0 20 20" aria-hidden="true">
        <rect x="1.5" y="4" width="17" height="12"/>
        <path d="M1.5 4l8.5 7 8.5-7M1.5 16l6-5.5M18.5 16l-6-5.5" fill="none" stroke="#f4f4f4" stroke-width="1.3"/>
      </svg>
      <span>support@quillbrook.me</span>
    </li>
  </ul>
</section>

</body>
</html>
```